UPDATE 2: I HAVE ATTACHED TWO PHOTOS; PLEASE CONSIDER USING EITHER ONE IN A NEW DESIGN. THANK YOU.
UPDATE: I HAVE INCLUDED 4 SAMPLE BOOK COVERS THAT I LIKE TO HELP YOU ORIENT YOUR DESIGN WORK
Looking for book cover, spine, and back for a MEMOIR. Details:
TITLE: Mama's Quiet Orchard
AUTHOR: Lorisha Pemberfeld
GENRE: Memoir
STYLE REQUESTED: Abstract and colorful; designers are welcome to get creative. Note that the memoir takes place largely in a poor African American city.
BOOK SUMMARY: As a young girl, Lorisha Pemberfeld—or “Rishi” to her friends and family—discovers the man she thought was her father wasn’t, and her real biological father wants little if anything to do with her. What follows is the story of a girl’s longing, a longing disturbed by abuse, disappointment, and loneliness.
Set against the backdrop of Gary, Indiana—the then “murder capital of the world”—Mama’s Quiet Orchard follows Lorisha as she searches and grows, following a path that eventually leads her to self-discovery and self-confidence.
Template provided for InDesign. Please note margins and bleed areas. Make sure any letters/words are at least one inch from edges. On spine, leave three inches at bottom for publisher's logo.
Updates
To all designers: Please note that there should NOT be any images of people as part of your designs. Thank you, and my apologies for not mentioning that in the initial ask.

```html
<!DOCTYPE html>
<html lang="en">
<head>
<meta charset="utf-8">
<title>Mama’s Quiet Orchard — Lorisha Pemberfeld</title>
<link href="https://fonts.googleapis.com/css2?family=Bebas+Neue&display=swap" rel="stylesheet">
<style>
  :root {
    --ink: #ffffff;
    --red: #c8140f;
    --deep-red: #8e0b0b;
    --orange: #ff5a0a;
    --green: #4fb02e;
    --blue: #1250b4;
    --violet: #5a2a8a;
  }
  html, body {
    margin: 0;
    padding: 0;
    overflow: hidden;
    background: #ffffff;
  }
  .cover {
    position: relative;
    width: 779px;
    height: 1200px;
    overflow: hidden;
    font-family: "Bebas Neue", "Oswald", sans-serif;
    color: var(--ink);
  }
  .cover-art {
    position: absolute;
    inset: 0;
    background:
      radial-gradient(ellipse 200px 260px at 380px 560px, rgba(79,176,46,0.95), rgba(79,176,46,0) 70%),
      radial-gradient(ellipse 160px 200px at 130px 420px, rgba(40,120,40,0.85), rgba(40,120,40,0) 70%),
      radial-gradient(ellipse 220px 120px at 200px 60px, rgba(255,90,10,0.9), rgba(255,90,10,0) 70%),
      radial-gradient(ellipse 180px 160px at 120px 860px, rgba(255,90,10,0.85), rgba(255,90,10,0) 70%),
      radial-gradient(ellipse 160px 180px at 620px 880px, rgba(255,110,20,0.8), rgba(255,110,20,0) 70%),
      radial-gradient(ellipse 300px 120px at 380px 1020px, rgba(18,80,180,0.95), rgba(18,80,180,0) 70%),
      radial-gradient(ellipse 240px 300px at 600px 450px, rgba(142,11,11,0.9), rgba(142,11,11,0) 70%),
      radial-gradient(ellipse 200px 140px at 420px 90px, rgba(60,10,10,0.85), rgba(60,10,10,0) 70%),
      radial-gradient(ellipse 300px 200px at 380px 1180px, rgba(200,20,15,0.85), rgba(200,20,15,0) 70%),
      linear-gradient(90deg, var(--blue) 0%, var(--violet) 8%, var(--red) 22%, var(--red) 78%, var(--violet) 92%, var(--blue) 100%);
  }
  .title {
    position: absolute;
    left: 0;
    right: 0;
    top: 158px;
    margin: 0;
    text-align: center;
    font-weight: 400;
    font-size: 123px;
    line-height: 148px;
    letter-spacing: 0.04em;
  }
  .title span { display: block; }
  .genre {
    position: absolute;
    left: 0;
    right: 0;
    top: 664px;
    margin: 0;
    text-align: center;
    font-size: 40px;
    line-height: 40px;
    letter-spacing: 0.16em;
  }
  .author {
    position: absolute;
    left: 0;
    right: 0;
    top: 803px;
    margin: 0;
    text-align: center;
    font-weight: 400;
    font-size: 115px;
    line-height: 141px;
    letter-spacing: 0.04em;
  }
  .author span { display: block; }
</style>
</head>
<body>
  <main class="cover">
    <div class="cover-art" role="img" aria-label="Abstract painted collage in red, orange, green and blue with a flock of dark birds in flight"></div>
    <h1 class="title">
      <span>Mama’s</span>
      <span>Quiet</span>
      <span>Orchard</span>
    </h1>
    <p class="genre">A Memoir</p>
    <h2 class="author">
      <span>Lorisha</span>
      <span>Pemberfeld</span>
    </h2>
  </main>
</body>
</html>
```